Looking to Redesign Brevonix.com website

You guys did one of the brochures for brevonix.com and I would like to see if we can go ahead and get an estimate for a redesigned web site for the company. We currently have a couple of pages on brevonix.com which are very much a starter type site.

The new design will need to reflect some of the things discussed in the brochure. It will have flash. Needs to be designed for simple hosting using cpanels.

The site needs to have between 12 and 15 pages with flash pages to move through features. Integrated with twitter like it is now, and contact forms delivered from our CRM along with other interactive features such as subscription to newsletter, etc...

I don't have lots of details on how to proceed yet, but here are some competitor sites:

Can we take a look at potential costs involved in the redo of the site as vague as my description above can permit.

Target Market(s)

Business to Business

Number of Pages Required

5+ page

Font styles to use
Sans Serif

Requirements
Must have
• Must have professional feel. Similar to brochure. and logo.
• Include our story in the discussion.
• embedded links to our CRM for popup contact forms.
• Logo files and 2 types of brochures uploaded.
• Important to keep color scheme
Nice to have
• Flash and some movement
Should not have
• Not sure yet

```html
<!DOCTYPE html>
<html lang="en">
<head>
<meta charset="utf-8">
<title>Brevonix – Hosted PBX Services</title>
<link rel="stylesheet" href="https://fonts.googleapis.com/css2?family=Open+Sans:wght@300;400;500;600;700&display=swap">
<style>
:root{
  --red:#b3131b;
  --black:#000;
  --ink:#222;
  --text:#666;
  --muted:#8a8a8a;
  --line:#dcdcdc;
  --panel:#f4f4f4;
  --white:#fff;
}
*{box-sizing:border-box;margin:0;padding:0}
html,body{width:959px;height:1200px;overflow:hidden;background:var(--white)}
body{position:relative;font-family:"Open Sans",sans-serif;color:var(--ink)}
a{color:inherit;text-decoration:none}
.abs{position:absolute}

/* header */
.brand{left:106px;top:22px;display:flex;align-items:center;gap:7px}
.brand-dot{width:36px;height:36px;border-radius:50%;background:var(--red)}
.brand-name{font-size:20px;font-weight:700;color:var(--red)}
.utility{right:106px;top:22px;display:flex;align-items:center;gap:8px;font-size:9.5px;color:var(--ink)}
.utility .sep{color:#999}
.social{width:14px;height:14px;border-radius:2px;margin-left:4px}
.social.one{background:#3b5998}
.social.two{background:#9a9a9a;margin-left:6px}
.main-nav{right:106px;top:58px;display:flex;gap:25px;font-size:10px;color:#333}
.main-nav .active{color:var(--red)}

/* hero */
.hero{left:0;top:89px;width:959px;height:440px;display:block}

/* welcome */
.welcome{left:106px;top:516px;width:748px}
.welcome h1{font-size:30px;font-weight:300;color:var(--red);line-height:1.2}
.welcome h1 strong{font-weight:700;color:var(--black)}
.welcome p{margin-top:10px;font-size:8.8px;line-height:16.8px;color:var(--text)}

/* services */
.services{left:105px;top:638px;width:748px;height:117px;background:var(--panel);border:1px solid var(--line)}
.service{position:absolute;top:17px;width:120px;margin-left:-60px;text-align:center}
.service .disc{width:56px;height:56px;border-radius:50%;background:var(--black);margin:0 auto;display:flex;align-items:center;justify-content:center}
.service span{display:block;margin-top:8px;font-size:13px;color:var(--red)}

/* benefits */
.benefits-title{left:0;width:959px;top:778px;text-align:center;font-size:32px;font-weight:300;color:var(--red)}
.benefit{position:absolute;width:170px}
.benefit svg{display:block;height:18px}
.benefit h3{margin-top:5px;font-size:12px;font-weight:500;color:var(--ink)}
.benefit p{margin-top:2px;font-size:7.4px;line-height:10px;color:var(--text)}
.vrule{position:absolute;width:1px;background:#e2e2e2}
.hrule{position:absolute;height:1px;background:#e2e2e2;top:910px}

/* footer */
.footer-wave{left:0;top:1016px;width:959px;height:184px}
.foot-brand{left:106px;top:1080px;display:flex;align-items:center;gap:5px;opacity:.55}
.foot-brand .brand-dot{width:22px;height:22px;background:#777}
.foot-brand .brand-name{font-size:12px;color:#999}
.contact{left:198px;top:1070px;font-size:13px;font-weight:300;color:#8f8f8f;line-height:24px}
.contact div{display:flex;align-items:center;gap:9px}
.foot-nav{left:106px;top:1140px;font-size:8.2px;color:#9a9a9a;display:flex;gap:5px}
.copyright{left:106px;top:1164px;font-size:8.2px;color:#9a9a9a}
.newsletter{left:666px;top:1126px;width:187px}
.newsletter h4{font-size:13px;font-weight:400;color:var(--white)}
.newsletter .field{margin-top:6px;height:28px;border:1px solid #777;display:flex;align-items:center;justify-content:space-between;padding:0 10px 0 11px;font-size:7.5px;color:#bbb}
</style>
</head>
<body>

<header>
  <a class="abs brand" href="#"><span class="brand-dot"></span><span class="brand-name">Brevonix</span></a>
  <div class="abs utility">
    <a href="#">SUPPORT</a><span class="sep">|</span><a href="#">CONTACT</a>
    <span class="social one"></span><span class="social two"></span>
  </div>
  <nav class="abs main-nav">
    <a class="active" href="#">Home</a><a href="#">About us</a><a href="#">Why Brevonix</a><a href="#">Features</a><a href="#">Advantages</a><a href="#">Best of Class Hardware</a>
  </nav>
</header>

<svg class="abs hero" viewBox="0 111 1199 550" preserveAspectRatio="none">
  <defs>
    <linearGradient id="heroTone" x1="0" y1="0" x2="1" y2="0.2">
      <stop offset="0" stop-color="#dfe1e2"/>
      <stop offset="0.38" stop-color="#d2d4d5"/>
      <stop offset="0.62" stop-color="#60636a"/>
      <stop offset="1" stop-color="#3b3e43"/>
    </linearGradient>
  </defs>
  <rect x="0" y="111" width="1199" height="550" fill="url(#heroTone)" role="img" aria-label="Photo of a conference speakerphone with an extension microphone on a desk"/>
  <rect x="0" y="305" width="25" height="32" fill="#9a9a9a" opacity=".6"/>
  <rect x="1174" y="305" width="25" height="32" fill="#555" opacity=".6"/>
  <path d="M17,313 L10,321 L17,329" stroke="#fff" stroke-width="1.5" fill="none"/>
  <path d="M1182,313 L1189,321 L1182,329" stroke="#fff" stroke-width="1.5" fill="none"/>
  <path d="M0,592 C150,537 300,507 450,522 C650,542 800,617 950,612 C1060,607 1150,562 1199,527 L1199,661 L0,661Z" fill="#fff"/>
  <path d="M0,602 C150,547 300,517 450,532 C650,552 800,627 950,622 C1060,617 1150,572 1199,537 L1199,661 L0,661Z" fill="var(--red)"/>
  <path d="M0,617 C150,562 300,532 450,546 C650,566 800,638 950,634 C1060,630 1150,583 1199,548 L1199,661 L0,661Z" fill="var(--black)"/>
  <path d="M0,660 C150,602 300,572 450,580 C650,594 800,652 950,650 C1060,647 1150,592 1199,564 L1199,661 L0,661Z" fill="#fff"/>
</svg>

<section class="abs welcome">
  <h1>Welcome to <strong>Brevonix</strong></h1>
  <p>Brevonix has been in the business of providing Hosted based PBX services since early 2003.&nbsp; This is before most of the business world had ever heard of such a service.<br>
  Yes.&nbsp; You may have never heard of us or our services...&nbsp; Fact is we have been providing services to corporate clients as a part of an IT managed services group and were not market-ing to other businesses.</p>
</section>

<section class="abs services">
  <div class="service" style="left:60px">
    <div class="disc"><svg width="30" height="30" viewBox="0 0 30 30"><circle cx="7" cy="23" r="3.5" fill="#fff"/><path d="M4,14 A12,12 0 0 1 16,26" stroke="#fff" stroke-width="3.5" fill="none"/><path d="M4,7 A19,19 0 0 1 23,26" stroke="#fff" stroke-width="3.5" fill="none"/></svg></div>
    <span>Wireless</span>
  </div>
  <div class="service" style="left:185px">
    <div class="disc"><svg width="34" height="24" viewBox="0 0 34 24"><rect x="1" y="1" width="32" height="22" fill="#fff"/><path d="M1,1 L17,14 L33,1 M1,23 L13,11 M33,23 L21,11" stroke="#000" stroke-width="1.6" fill="none"/></svg></div>
    <span>Email</span>
  </div>
  <div class="service" style="left:310px">
    <div class="disc"><svg width="34" height="30" viewBox="0 0 34 30"><path d="M17,2 C26,2 33,8 33,14 C33,20 26,26 17,26 C15,26 13,26 11,25 L4,29 L6,22 C3,20 1,17 1,14 C1,8 8,2 17,2Z" fill="#fff"/><circle cx="10" cy="14" r="2.3"/><circle cx="17" cy="14" r="2.3"/><circle cx="24" cy="14" r="2.3"/></svg></div>
    <span>Text Messaging</span>
  </div>
  <div class="service" style="left:436px">
    <div class="disc"><svg width="34" height="34" viewBox="0 0 34 34"><circle cx="17" cy="17" r="15" fill="#fff"/><path d="M6,10 C12,12 12,18 8,24 M20,3 C17,9 22,13 29,12 M15,31 C16,24 22,21 31,22 M12,15 L22,20" stroke="#000" stroke-width="2.2" fill="none"/></svg></div>
    <span>Web</span>
  </div>
  <div class="service" style="left:561px">
    <div class="disc"><svg width="32" height="30" viewBox="0 0 32 30"><rect x="8" y="1" width="16" height="8" fill="#fff"/><rect x="1" y="10" width="30" height="12" rx="2" fill="#fff"/><rect x="8" y="18" width="16" height="11" fill="#fff" stroke="#000" stroke-width="1.5"/><rect x="25" y="13" width="3" height="2" fill="#000"/></svg></div>
    <span>Fax</span>
  </div>
  <div class="service" style="left:687px">
    <div class="disc"><svg width="20" height="32" viewBox="0 0 20 32"><rect x="1" y="1" width="18" height="30" rx="3" fill="#fff"/><rect x="3.5" y="5" width="13" height="19" fill="#000"/><circle cx="10" cy="27.5" r="1.6" fill="#000"/></svg></div>
    <span>Phone</span>
  </div>
</section>

<h2 class="abs benefits-title">Benefits</h2>

<div class="vrule" style="left:293px;top:840px;height:57px"></div>
<div class="vrule" style="left:478px;top:840px;height:57px"></div>
<div class="vrule" style="left:666px;top:840px;height:57px"></div>
<div class="vrule" style="left:293px;top:925px;height:57px"></div>
<div class="vrule" style="left:478px;top:925px;height:57px"></div>
<div class="vrule" style="left:666px;top:925px;height:57px"></div>
<div class="hrule" style="left:105px;width:178px"></div>
<div class="hrule" style="left:303px;width:167px"></div>
<div class="hrule" style="left:489px;width:167px"></div>
<div class="hrule" style="left:678px;width:175px"></div>

<div class="benefit" style="left:128px;top:842px">
  <svg viewBox="0 0 20 20" width="18"><circle cx="10" cy="10" r="8" stroke="var(--red)" stroke-width="2.4" fill="none"/><path d="M10,5 V10 H6" stroke="var(--red)" stroke-width="2" fill="none"/></svg>
  <h3>Quick ROI</h3><p>Equipment is included in the service</p>
</div>
<div class="benefit" style="left:354px;top:842px">
  <svg viewBox="0 0 16 20" width="15"><path d="M1,2 H15 V10 C15,15 11,18 8,19 C5,18 1,15 1,10Z" fill="var(--red)"/><path d="M8,4 H12 V10 C12,13 10,15 8,16Z" fill="#fff"/></svg>
  <h3>Secure</h3><p>Encrypted Lines</p>
</div>
<div class="benefit" style="left:502px;top:842px">
  <svg viewBox="0 0 26 22" width="24"><circle cx="9" cy="13" r="6" stroke="var(--red)" stroke-width="3.5" stroke-dasharray="2.4 1.4" fill="none"/><circle cx="9" cy="13" r="2" fill="var(--red)"/><circle cx="20" cy="6" r="4" stroke="var(--red)" stroke-width="2.6" stroke-dasharray="1.8 1.2" fill="none"/><circle cx="20" cy="17" r="3.5" stroke="var(--red)" stroke-width="2.4" stroke-dasharray="1.6 1.1" fill="none"/></svg>
  <h3>Easy Installation</h3><p>Very little business interruption</p>
</div>
<div class="benefit" style="left:714px;top:842px">
  <svg viewBox="0 0 28 22" width="27"><g fill="var(--red)" stroke="#fff" stroke-width="1"><path d="M9,2 L15,0 L21,2 L21,9 L15,11 L9,9Z"/><path d="M2,11 L8,9 L14,11 L14,18 L8,20 L2,18Z"/><path d="M14,11 L20,9 L26,11 L26,18 L20,20 L14,18Z"/></g></svg>
  <h3>Expandable</h3><p>One unit at a time</p>
</div>
<div class="benefit" style="left:128px;top:925px">
  <svg viewBox="0 0 20 20" width="19"><path d="M2,18 L10,10" stroke="var(--red)" stroke-width="3.5" stroke-linecap="round"/><path d="M10,10 A5,5 0 1 1 17,4 L13,5 L14,8 L18,6 A5,5 0 0 1 10,10Z" fill="var(--red)"/></svg>
  <h3>Customized</h3><p>Expandable speed-dial options</p>
</div>
<div class="benefit" style="left:354px;top:925px">
  <svg viewBox="0 0 24 16" width="23"><rect x="1" y="2" width="22" height="12" rx="1" stroke="var(--red)" stroke-width="1.6" fill="none"/><path d="M4,6 H20 M4,9 H20 M7,12 H17" stroke="var(--red)" stroke-width="1.5" stroke-dasharray="1.6 1"/></svg>
  <h3>Intuitive</h3><p>Easy to learn and use</p>
</div>
<div class="benefit" style="left:502px;top:925px">
  <svg viewBox="0 0 22 22" width="20"><rect x="1" y="1" width="11" height="8" rx="4" transform="rotate(40 6 5)" stroke="var(--red)" stroke-width="2.4" fill="none"/><rect x="10" y="12" width="11" height="8" rx="4" transform="rotate(40 15 16)" stroke="var(--red)" stroke-width="2.4" fill="none"/><path d="M8,8 L14,14" stroke="var(--red)" stroke-width="2.4"/></svg>
  <h3>Builtin Fail-Over</h3><p>Calls go throught even if a supplier phone company has outages</p>
</div>
<div class="benefit" style="left:714px;top:925px">
  <svg viewBox="0 0 16 20" width="14"><path d="M4,9 V6 A4,4 0 0 1 12,6 V9" stroke="var(--red)" stroke-width="2.4" fill="none"/><rect x="1" y="9" width="14" height="10" rx="1.5" fill="var(--red)"/></svg>
  <h3>Safety</h3><p>911 notification to managers</p>
</div>

<svg class="abs footer-wave" viewBox="0 1270 1199 230" preserveAspectRatio="none">
  <path d="M0,1335 C120,1300 230,1280 340,1278 C520,1276 700,1372 900,1378 C1020,1382 1120,1335 1199,1302 L1199,1500 L0,1500Z" fill="var(--red)"/>
  <path d="M0,1346 C120,1312 230,1292 340,1290 C520,1288 700,1382 900,1388 C1020,1392 1120,1346 1199,1314 L1199,1500 L0,1500Z" fill="#fff"/>
  <path d="M0,1350 C120,1317 230,1297 340,1295 C520,1293 700,1387 900,1393 C1020,1397 1120,1351 1199,1319 L1199,1500 L0,1500Z" fill="var(--black)"/>
</svg>

<footer>
  <div class="abs foot-brand"><span class="brand-dot"></span><span class="brand-name">Brevonix</span></div>
  <div class="abs contact">
    <div><svg width="10" height="10" viewBox="0 0 10 10"><path d="M2,0.5 L4,2.8 L3,4 C3.8,5.6 4.6,6.4 6,7 L7.2,6 L9.5,8 L8,9.5 C4,9 1,6 0.5,2Z" fill="#8f8f8f"/></svg><span>Phone : +1 555 018 4660</span></div>
    <div><svg width="10" height="8" viewBox="0 0 10 8"><rect width="10" height="8" fill="#8f8f8f"/><path d="M0,0 L5,4.5 L10,0" stroke="#000" stroke-width="1" fill="none"/></svg><span>Email : sales@brevonix.com</span></div>
  </div>
  <nav class="abs foot-nav">
    <a href="#">Home</a><span>|</span><a href="#">About us</a><span>|</span><a href="#">Why Brevonix</a><span>|</span><a href="#">Features</a><span>|</span><a href="#">Advantages</a><span>|</span><a href="#">Best of Class Hardware</a>
  </nav>
  <p class="abs copyright">Copyright &copy; 2016 &nbsp;Brevonix. &nbsp;All rights reserved.</p>
  <form class="abs newsletter">
    <h4>Newsletter Subscribe</h4>
    <div class="field"><span>Email ID</span><svg width="13" height="10" viewBox="0 0 13 10"><rect width="13" height="10" fill="#aaa"/><path d="M0,0 L6.5,5.5 L13,0" stroke="#000" stroke-width="1.2" fill="none"/></svg></div>
  </form>
</footer>

</body>
</html>
```